Web page design for a startup, no coding

Quorvix is a Data mining startup helping companies get data from websites. We’re looking to revamp our website to make it more professional and conversation friendly.
I need a designer to design the website in PSD and Once the PSD is done, the HTML design will be awarded as a separate job. We’ll need continues improvements to the design based on the user behaviour in the site and this can be a long term work for the right designer.
Read the details on the attached document
Target Market(s)
Big data, Data Mining
Industry/Entity Type
Business Software
Number of Pages Required
5+ page
Requirements
Must have
- Refer to the doc
Nice to have
- Refer to the doc
Should not have
- Refer to the doc

```html
<!DOCTYPE html>
<html lang="en">
<head>
<meta charset="utf-8">
<title>Quorvix – Structured Data Feeds</title>
<link href="https://fonts.googleapis.com/css2?family=Roboto:wght@300;400;500;700&display=swap" rel="stylesheet">
<style>
:root{
  --gold:#f5b800;
  --navy:#0f2a52;
  --navy-deep:#0a1a36;
  --ink:#333;
  --muted:#777;
  --light:#e6e6e6;
  --dark:#141414;
  --white:#fff;
  --blue-link:#2e9bd6;
}
*{margin:0;padding:0;box-sizing:border-box}
html,body{width:1200px;height:3340px;overflow:hidden}
body{font-family:'Roboto',Arial,sans-serif;color:var(--ink);background:var(--white);position:relative}
.abs{position:absolute}
.center{text-align:center;left:0;width:1200px}

/* header */
.site-header{position:absolute;top:0;left:0;width:1200px;height:110px;background:var(--white);z-index:3}
.brand{position:absolute;left:89px;top:36px;display:flex;align-items:center;gap:10px;font-size:30px;font-weight:400;color:#222}
.brand-mark{width:26px;height:26px;border:2px solid #222}
.main-nav{position:absolute;top:34px;left:617px;display:flex;align-items:center}
.main-nav a{font-size:14px;font-weight:500;color:#222;text-decoration:none;margin-right:44px;padding:12px 14px}
.main-nav a.active{color:var(--gold);border:1px solid var(--gold);border-radius:4px}

/* hero */
.hero{position:absolute;top:110px;left:0;width:1200px;height:555px}
.hero h1{position:absolute;top:195px;left:0;width:1200px;text-align:center;color:var(--white);font-size:34px;font-weight:500}
.hero p{position:absolute;top:245px;left:300px;width:600px;text-align:center;color:#dfe7f3;font-size:14px;line-height:24px}
.btn-ghost{position:absolute;top:306px;left:527px;width:145px;height:40px;border:1.5px solid var(--white);border-radius:4px;color:var(--white);font-size:13px;font-weight:500;display:flex;align-items:center;justify-content:center}
.slide-arrow{position:absolute;color:var(--white);font-size:40px;font-weight:300}

/* section heads */
.section-title{position:absolute;left:0;width:1200px;text-align:center;font-size:26px;font-weight:500;color:#333}
.divider{position:absolute;left:535px;width:130px;height:20px}

/* why */
.why-card{position:absolute;top:848px;width:230px;text-align:center}
.why-card .photo{width:230px;height:185px}
.why-card h3{margin-top:26px;font-size:16px;font-weight:500;color:#222}
.why-card p{margin-top:8px;font-size:12px;line-height:22px;color:#666;padding:0 14px}
.btn-small{display:inline-block;margin-top:12px;width:100px;height:32px;line-height:30px;border:1px solid var(--gold);border-radius:4px;color:var(--gold);font-size:11px;font-weight:500}

/* offerings */
.offerings{position:absolute;top:1226px;left:0;width:1200px;height:513px;background:linear-gradient(180deg,#1c1c1c,#0e0e0e)}
.offer{position:absolute;top:1560px;width:320px;text-align:center;color:#ddd}
.offer h3{color:var(--gold);font-size:17px;font-weight:500}
.offer p{margin-top:6px;font-size:12.5px;line-height:24px}
.offer .more{margin-top:4px;font-size:13px;font-weight:700;color:var(--white)}
.lead{color:#ddd;font-size:15px;line-height:24px}

/* help */
.help{position:absolute;top:1739px;left:0;width:1200px;height:543px;background:var(--light)}
.field{position:absolute;background:var(--white);border:1px solid #ccc;font-size:12px;color:#999;padding:0 26px;display:flex;align-items:center}
.btn-submit{position:absolute;top:2148px;left:534px;width:132px;height:42px;background:#cfcfcf;border:1px solid #b5b5b5;border-radius:4px;font-size:12px;font-weight:500;color:#333;display:flex;align-items:center;justify-content:center}

/* testimonials */
.testimonials{position:absolute;top:2282px;left:0;width:1200px;height:398px;background:linear-gradient(90deg,#161616,#262a30 60%,#15181c)}
.quote{position:absolute;top:2450px;left:481px;width:430px;color:var(--white);font-size:15px;line-height:26px}
.quote cite{display:block;margin-top:4px;color:var(--gold);font-style:normal;font-weight:700;font-size:14px}
.dot{position:absolute;top:2598px;width:11px;height:11px;border-radius:50%;background:var(--white)}

/* clients */
.client{position:absolute;top:2872px;font-size:28px;font-weight:500;color:#2a4f8a}

/* footer */
.footer{position:absolute;top:2927px;left:0;width:1200px;height:413px;background:var(--light)}
.footer h4{position:absolute;top:3086px;font-size:15px;font-weight:500;color:#333}
.links{position:absolute;top:3122px;list-style:none;font-size:13px;color:#555;line-height:23.5px}
.links li::before{content:"\00BB";color:var(--blue-link);margin-right:10px}
.social li::before{content:"";display:inline-block;width:13px;height:13px;background:var(--blue-link);margin-right:14px;vertical-align:-2px}
.btn-sub{position:absolute;top:3179px;left:817px;width:104px;height:40px;background:var(--gold);font-size:12px;font-weight:500;color:#222;display:flex;align-items:center;justify-content:center}
</style>
</head>
<body>

<header class="site-header">
  <div class="brand"><span class="brand-mark"></span>Quorvix</div>
  <nav class="main-nav">
    <a class="active">SOLUTIONS</a><a>PRICING</a><a>COMPANY</a><a>GET FREE QUOTE</a>
  </nav>
</header>

<section class="hero">
  <svg class="abs" style="top:0;left:0" width="1200" height="555" viewBox="0 0 1200 555">
    <defs>
      <linearGradient id="heroBg" x1="0" y1="0" x2="0" y2="1">
        <stop offset="0" stop-color="#355a8a"/>
        <stop offset="0.25" stop-color="#163663"/>
        <stop offset="1" stop-color="#0b1f40"/>
      </linearGradient>
    </defs>
    <polygon points="0,0 1200,0 1200,435 600,552 0,435" fill="url(#heroBg)"/>
    <polyline points="0,435 600,552 1200,435" fill="none" stroke="#f5b800" stroke-width="3"/>
    <rect role="img" aria-label="Illustration of a tablet with an iceberg of data rising from it" x="150" y="0" width="900" height="125" fill="#9fb3cc" opacity="0.35"/>
  </svg>
  <h1>TURN WEBSITES INTO STRUCTURED DATA FEEDS</h1>
  <p>Easily get structured data feeds from any website through our cloud base data as a service platform. No programming ,Servers or Expensive Softwares required.</p>
  <div class="btn-ghost">GET FREE QUOTE</div>
  <div class="slide-arrow" style="left:28px;top:238px">&#8249;</div>
  <div class="slide-arrow" style="left:1148px;top:238px">&#8250;</div>
</section>

<h2 class="section-title" style="top:732px">WHY QUORVIX</h2>
<svg class="divider" style="top:770px" viewBox="0 0 130 20"><line x1="0" y1="10" x2="50" y2="10" stroke="#f5b800" stroke-width="2"/><rect x="58" y="3" width="14" height="14" fill="none" stroke="#999" stroke-width="1.5"/><line x1="80" y1="10" x2="130" y2="10" stroke="#f5b800" stroke-width="2"/></svg>

<div class="why-card" style="left:89px"><div class="photo" role="img" aria-label="Photo of stressed office workers" style="background:linear-gradient(135deg,#d7d9dc,#6b7077)"></div><h3>SOLVE REAL PROBLEMS</h3><p>Quorvix provides a fully managed Big you can easily data as Service</p><span class="btn-small">READ MORE</span></div>
<div class="why-card" style="left:352px"><div class="photo" role="img" aria-label="Photo of a hand touching glowing data icons" style="background:radial-gradient(circle at 40% 50%,#1f8a8a,#050f14 70%)"></div><h3>CLEAN DATA</h3><p>We follow a strict quality assurance process and the data integrity.</p><span class="btn-small">READ MORE</span></div>
<div class="why-card" style="left:617px"><div class="photo" role="img" aria-label="Photo of hands holding a tablet" style="background:linear-gradient(135deg,#e9b996,#a85c3a)"></div><h3>CUSTOMER SUCCESS</h3><p>Ensuring Customer success is our first priority team consists data</p><span class="btn-small">READ MORE</span></div>
<div class="why-card" style="left:881px"><div class="photo" role="img" aria-label="Photo of glowing binary code" style="background:linear-gradient(135deg,#1d5fb3,#0a1d3f)"></div><h3>DATA WRANGLING SUPPORT</h3><p>Quorvix helps those who need data wrangling by providing profiling</p><span class="btn-small">READ MORE</span></div>

<section class="offerings"></section>
<h2 class="section-title" style="top:1291px;color:#fff">OUR OFFERINGS</h2>
<svg class="divider" style="top:1331px" viewBox="0 0 130 20"><line x1="0" y1="10" x2="50" y2="10" stroke="#f5b800" stroke-width="2"/><rect x="58" y="3" width="14" height="14" fill="none" stroke="#ccc" stroke-width="1.5"/><line x1="80" y1="10" x2="130" y2="10" stroke="#f5b800" stroke-width="2"/></svg>
<p class="lead abs center" style="top:1366px">Businesses of all sizes use our clean data feeds to Quickly build apps, Experiment<br>with fresh ideas and Solve business problems.</p>
<svg class="abs" style="top:1455px;left:0" width="1200" height="110" viewBox="0 0 1200 110">
  <line x1="306" y1="54" x2="540" y2="54" stroke="#f5b800" stroke-width="1.5" stroke-dasharray="3 4"/>
  <line x1="656" y1="54" x2="878" y2="54" stroke="#f5b800" stroke-width="1.5" stroke-dasharray="3 4"/>
  <g fill="none" stroke="#f5b800" stroke-width="2">
    <polygon points="222,6 276,6 303,54 276,102 222,102 195,54"/>
    <polygon points="572,6 626,6 653,54 626,102 572,102 545,54"/>
    <polygon points="908,6 962,6 989,54 962,102 908,102 881,54"/>
    <path d="M232 42h8l6 20h20l4-14h-27M250 70a3 3 0 1 0 .1 0M264 70a3 3 0 1 0 .1 0"/>
    <circle cx="599" cy="46" r="7"/><path d="M587 66q12-12 24 0"/>
    <path d="M925 70l10-14 10 6 8-18M945 44h10v10"/>
  </g>
  <text x="32" y="70" fill="#fff" font-size="40" font-family="Roboto,sans-serif" font-weight="300">&#8249;</text>
  <text x="1148" y="70" fill="#fff" font-size="40" font-family="Roboto,sans-serif" font-weight="300">&#8250;</text>
</svg>
<div class="offer" style="left:89px"><h3>E-COMMERCE</h3><p>Our Ecommerce product data feeds gives you access to structured product information like pricing</p><div class="more">READ MORE &gt;&gt;</div></div>
<div class="offer" style="left:439px"><h3>LEAD GENERATION</h3><p>We help find quality leads for your business by extracting public data like ProLinks,</p><div class="more">READ MORE &gt;&gt;</div></div>
<div class="offer" style="left:775px"><h3>SERP TRACKING</h3><p>Our SERP data feeds gives companies access to Search Engine of any keywords</p><div class="more">READ MORE &gt;&gt;</div></div>

<section class="help"></section>
<div class="abs" role="img" aria-label="Faint world map" style="top:1995px;left:880px;width:240px;height:140px;background:radial-gradient(ellipse at center,#cfcfcf,#e6e6e6 70%)"></div>
<h2 class="section-title" style="top:1798px">WE'RE HERE TO HELP!</h2>
<svg class="divider" style="top:1838px" viewBox="0 0 130 20"><line x1="0" y1="10" x2="50" y2="10" stroke="#f5b800" stroke-width="2"/><rect x="58" y="3" width="14" height="14" fill="none" stroke="#999" stroke-width="1.5"/><line x1="80" y1="10" x2="130" y2="10" stroke="#f5b800" stroke-width="2"/></svg>
<p class="abs center" style="top:1880px;font-size:14px;line-height:23px;color:#888">We pride ourselves on being a customer first company - I hope you'll let us prove it to you. Fill<br>the form below to setup a consultation and get a free quote.</p>
<div class="field" style="top:1957px;left:309px;width:339px;height:40px">Your Email Address..</div>
<div class="field" style="top:1957px;left:666px;width:224px;height:40px;justify-content:space-between">Your monthly Budget<span>&#9662;</span></div>
<div class="field" style="top:2017px;left:309px;width:581px;height:109px;align-items:flex-start;padding-top:16px">Drop us a line or two. We will get back to you Sooo...</div>
<div class="btn-submit">SUBMIT MESSAGE</div>
<p class="abs center" style="top:2203px;font-size:11px;color:#555">*Please fill all required form fields, thanks!</p>

<section class="testimonials"></section>
<h2 class="section-title" style="top:2342px;color:#fff">TESTIMONIALS</h2>
<svg class="divider" style="top:2381px" viewBox="0 0 130 20"><line x1="0" y1="10" x2="50" y2="10" stroke="#f5b800" stroke-width="2"/><rect x="58" y="3" width="14" height="14" fill="none" stroke="#ccc" stroke-width="1.5"/><line x1="80" y1="10" x2="130" y2="10" stroke="#f5b800" stroke-width="2"/></svg>
<svg class="abs" style="top:2440px;left:268px" width="180" height="115" viewBox="0 0 180 115">
  <circle cx="50" cy="57" r="49" fill="#d6d6d6"/>
  <text x="34" y="72" font-size="44" font-family="Roboto,sans-serif" font-weight="700" fill="#fff">&#8220;</text>
  <circle role="img" aria-label="Portrait of the customer" cx="126" cy="57" r="52" fill="#8a8f96" stroke="#fff" stroke-width="3"/>
</svg>
<div class="quote">“Quorvix provided us with great service and interactions in a very short amount of time. Even though it was not obvious to extract the data, Quorvix managedes”<cite>- Marek Tolland - CEO&amp;Founder @Velmora</cite></div>
<span class="dot" style="left:578px;background:var(--gold)"></span><span class="dot" style="left:596px"></span><span class="dot" style="left:614px"></span><span class="dot" style="left:632px"></span><span class="dot" style="left:650px"></span>

<section class="footer"></section>
<svg class="abs" style="top:2680px;left:0" width="1200" height="345" viewBox="0 0 1200 345"><polygon points="0,0 1200,0 1200,247 600,343 0,247" fill="#fff"/></svg>
<h2 class="section-title" style="top:2742px">OUR CLIENTS</h2>
<svg class="divider" style="top:2782px" viewBox="0 0 130 20"><line x1="0" y1="10" x2="50" y2="10" stroke="#f5b800" stroke-width="2"/><rect x="58" y="3" width="14" height="14" fill="none" stroke="#999" stroke-width="1.5"/><line x1="80" y1="10" x2="130" y2="10" stroke="#f5b800" stroke-width="2"/></svg>
<div class="client" style="left:268px">Norvane</div>
<div class="client" style="left:445px">Brixel</div>
<div class="client" style="left:630px">Lumacore</div>
<div class="client" style="left:822px">Taskwell</div>

<h4 style="left:87px">QUICK LINKS</h4>
<ul class="links" style="left:87px"><li>Solutions</li><li>Pricing</li><li>Company</li><li>Get free Quote</li></ul>
<h4 style="left:267px">OTHER LINKS</h4>
<ul class="links" style="left:267px"><li>Blog</li><li>Answers</li><li>Case Studies</li><li>Slide</li></ul>
<ul class="links" style="left:396px"><li>Startup Partner program</li><li>FAQ</li><li>Careers</li><li>Social media link</li></ul>
<h4 style="left:626px">OTHER LINKS</h4>
<ul class="links social" style="left:626px"><li>Circlebook</li><li>Chirper</li><li>Searchly plus</li><li>Pinboardly</li></ul>
<h4 style="left:817px">SUBSCRIBE TO OUR BLOG</h4>
<div class="field" style="top:3128px;left:817px;width:296px;height:40px;padding:0 14px">Email Address...</div>
<div class="btn-sub">SUBSCRIBE</div>
<div class="abs" style="top:3268px;left:87px;width:1026px;height:1px;background:#cfcfcf"></div>
<p class="abs center" style="top:3294px;font-size:12px;color:#555">@copyright 2016 Quorvix. All rights Reserved</p>

</body>
</html>
```